Create the design of Sitelaunch (in photoshop or similar)

*edit* What we wanna see is a sketch of a first page, and then in the end 5 page designs, but the main page will be the big tasks other pages are just basically pop-ups or form. *edit*

We need a web design for our new startup Sitelaunch in turn will be providing web pages to smaller business. So the purpose of the page is to clearly showcase the message in a web 3.0 fashion, good design looks but function should always be the main focus.Further more we are looking for a long term relationship with a good designer / design company that can help us design the future web sites for our customers as well.

We need you to understand web, not just design. You need to be up to date with how web looks and works, and how to make it as simple and easy to use as possible for the customer and at the same time good looking.

Colors and layout are free to choose, but we really like the kind of layout that forkcomet.com has so feel free to be inspired by them.

We want all of the pages design, but the main/landing page will be the big part, the rest are small pages that will use the same design frame as the main page.

PS. We just want the design in photoshop or illustrator format, the website will then be built in word press by word press experts (let us know if you/company also possess this knowledge)

Target Market(s)

Small to medium sized business, mostly owner/entrepreneur driven companies.

Industry/Entity Type

Business

Font styles to use
Other font styles liked:
• Helvetica for the win

Requirements
Must have
• Great and simple design, a child should be able to understand the message and also enjoy reading it. Should be a funny website while still being professional, i.e. see postbadger.com for example.

```html
<!DOCTYPE html>
<html lang="en">
<head>
<meta charset="utf-8">
<title>Sitelaunch – Most convenient web ever</title>
<link rel="stylesheet" href="https://fonts.googleapis.com/css2?family=Arimo:wght@400;700&display=swap">
<style>
:root{
  --red:#c1272d;
  --red-deep:#b01f24;
  --ink:#333333;
  --muted:#666666;
  --faint:#b5b5b5;
  --card:#f2f2f2;
  --page:#f9f9f9;
  --dark:#2b2b2b;
  --white:#ffffff;
  --line:#dcdcdc;
}
*{box-sizing:border-box;margin:0;padding:0}
html,body{width:760px;height:1200px;overflow:hidden}
body{font-family:"Arimo",Helvetica,Arial,sans-serif;background:var(--page);color:var(--ink);position:relative}
.topbar{position:absolute;left:0;top:0;width:760px;height:48px;background:var(--red)}
.brand{position:absolute;left:83px;top:10px;color:var(--white)}
.brand-name{font-size:19px;font-weight:400;letter-spacing:.3px;line-height:20px}
.brand-tag{font-size:8.5px;margin-left:4px;line-height:12px}
.main-nav{position:absolute;left:270px;top:18px;display:flex;gap:14px;font-size:7.5px;color:var(--white)}
.subbar{position:absolute;left:0;top:48px;width:760px;height:40px;background:var(--white)}
.perks{position:absolute;left:84px;top:17px;display:flex;gap:30px;font-size:7.5px;color:var(--muted)}
.lang{position:absolute;left:505px;top:9px;width:84px;height:22px;background:#efefef;border:1px solid var(--line);display:flex;align-items:center;gap:5px;padding-left:9px;font-size:9px;color:var(--muted)}
.flag{width:16px;height:11px;background:#2a3f8f;position:relative}
.flag::before,.flag::after{content:"";position:absolute;background:var(--red)}
.flag::before{left:0;top:4px;width:16px;height:3px}
.flag::after{left:6px;top:0;width:4px;height:11px}
.chat{position:absolute;left:598px;top:9px;width:80px;height:22px;background:#efefef;border:1px solid var(--line);display:flex;align-items:center;gap:5px;padding-left:8px;font-size:9.5px;font-weight:700;color:var(--ink)}
.hero{position:absolute;left:0;top:88px;width:760px;height:262px;background:radial-gradient(ellipse at 55% 20%,#4a5f8e 0%,#263452 45%,#1a2236 100%);overflow:hidden}
.hero-photo{position:absolute;left:400px;top:0;width:360px;height:262px;background:linear-gradient(100deg,rgba(60,80,130,0) 0%,#3d4f7a 25%,#2c2f3a 70%,#1e2128 100%)}
.hero-copy{position:absolute;left:83px;top:68px;width:290px;color:var(--white)}
.hero-title{font-size:30px;font-weight:700;letter-spacing:.5px;line-height:32px}
.hero-sub{font-size:13.5px;margin-top:6px;font-weight:400}
.hero-text{font-size:6.2px;line-height:12px;margin-top:9px;color:#d8dce6}
.btn{display:inline-flex;align-items:center;justify-content:center;background:var(--red);color:var(--white);font-weight:700}
.hero-btn{margin-top:12px;width:139px;height:28px;font-size:8px}
.slide-arrow{position:absolute;top:122px}
.card{position:absolute;background:var(--card);width:281px}
.card-a{left:82px;top:382px;height:263px}
.card-b{left:397px;top:382px;height:263px}
.card-c{left:82px;top:674px;height:322px}
.card-d{left:397px;top:674px;height:322px}
.badge{position:absolute;left:68px;top:18px;width:126px;height:126px;border-radius:50%;border:1px solid #d6d6d6;display:flex;align-items:center;justify-content:center}
.badge-inner{width:93px;height:93px;border-radius:50%;background:#e4e4e4;display:flex;align-items:center;justify-content:center}
.card-title{position:absolute;left:0;top:164px;width:100%;text-align:center;font-size:16px;font-weight:400;color:var(--ink)}
.points{position:absolute;left:20px;top:195px;width:222px;list-style:none;font-size:10.5px;color:var(--muted);line-height:13px}
.points li{display:flex;gap:8px;margin-bottom:8px}
.points svg{flex:none;margin-top:2px}
.order-btn{position:absolute;left:202px;top:224px;width:50px;height:17px;font-size:8px}
.partner{position:absolute;left:55px;top:262px;width:153px;height:38px;background:var(--white);border:1px solid #d2d2d2;display:flex;align-items:center;justify-content:center;font-size:13px;font-weight:400;color:var(--ink)}
.calc-title{position:absolute;left:0;top:26px;width:100%;text-align:center;font-size:16.5px;font-weight:400}
.calc-sub{position:absolute;left:0;top:49px;width:100%;text-align:center;font-size:9px}
.field{position:absolute;left:17px;width:250px}
.field label{display:block;font-size:7.5px;color:var(--muted)}
.field .box{position:absolute;left:0;top:12px;width:83px;height:17px;background:var(--white);border:1px solid #d6d6d6;font-size:8px;color:var(--red);padding:3px}
.field .hint{position:absolute;left:92px;top:11px;width:160px;font-size:5.8px;line-height:8.5px;color:var(--faint)}
.calc-btn{position:absolute;left:61px;top:263px;width:152px;height:37px;font-size:15px;font-weight:400}
.cta-band{position:absolute;left:0;top:1048px;width:760px;height:65px;background:var(--red-deep)}
.cta{position:absolute;left:110px;top:13px;width:539px;height:38px;background:#cc1f1f;color:var(--white);display:flex;align-items:center;justify-content:center;font-size:13.5px}
.footer{position:absolute;left:0;top:1113px;width:760px;height:87px;background:var(--dark);color:var(--white)}
.foot-nav{position:absolute;left:0;top:19px;width:100%;text-align:center;font-size:8px}
.copy{position:absolute;left:0;top:41px;width:100%;text-align:center;font-size:6.5px;color:#aaaaaa}
.social{position:absolute;left:327px;top:60px;display:flex;gap:5px}
.social span{width:17px;height:17px;display:block}
</style>
</head>
<body>
<header class="topbar">
  <div class="brand"><div class="brand-name">SITE LAUNCH</div><div class="brand-tag">most convenient web ever</div></div>
  <nav class="main-nav"><span>Home</span><span>How it Works</span><span>About Us</span><span>FAQs</span><span>Privacy Policy</span><span>What Pepople Think ?</span><span>Order</span><span>Contact Us</span></nav>
</header>
<div class="subbar">
  <div class="perks"><span>Free unlimited Support</span><span>Free updates</span><span>Need Help</span></div>
  <div class="lang"><span class="flag"></span>English <svg width="8" height="6" viewBox="0 0 8 6" style="margin-left:6px"><path d="M1 1l3 3 3-3" fill="none" stroke="#666" stroke-width="1.3"/></svg></div>
  <div class="chat"><svg width="16" height="13" viewBox="0 0 16 13"><path d="M2 1h10a2 2 0 012 2v4a2 2 0 01-2 2H7l-4 3V9H2a2 2 0 01-2-2V3a2 2 0 012-2z" fill="#c1272d"/></svg>Live Chat</div>
</div>
<section class="hero">
  <div class="hero-photo" role="img" aria-label="Photo of a man in a suit pointing at a white sign with a question mark, over a dotted world map"></div>
  <div class="hero-copy">
    <h1 class="hero-title">SITELAUNCH</h1>
    <p class="hero-sub">Most Convenient Meal at sitelaunch</p>
    <p class="hero-text">our mission is to make people Happy by delivering delicious meals made with fresh Fresh Ingredients at the speed of Light. we're dedicated to helping the world through our meal matching program. for we donate one to a child in need......</p>
    <span class="btn hero-btn">CLICK HERE FOR MORE INFO</span>
  </div>
  <svg class="slide-arrow" style="left:11px" width="24" height="24" viewBox="0 0 24 24"><circle cx="12" cy="12" r="10.5" fill="none" stroke="#fff" stroke-width="1.6"/><path d="M14 7l-5 5 5 5z" fill="#fff"/></svg>
  <svg class="slide-arrow" style="left:721px" width="24" height="24" viewBox="0 0 24 24"><circle cx="12" cy="12" r="10.5" fill="none" stroke="#fff" stroke-width="1.6"/><path d="M10 7l5 5-5 5z" fill="#fff"/></svg>
</section>

<article class="card card-a">
  <div class="badge"><div class="badge-inner"><svg width="50" height="56" viewBox="0 0 50 56"><path d="M4 44l14-14 6 6-14 14z" fill="#555"/><text x="22" y="46" font-family="Arimo,sans-serif" font-size="52" font-weight="700" fill="#c1272d">?</text></svg></div></div>
  <h2 class="card-title">WHAT IS SITELAUNCH?</h2>
  <ul class="points">
    <li><svg width="9" height="9" viewBox="0 0 9 9"><circle cx="4.5" cy="4.5" r="3.8" fill="none" stroke="#c1272d"/><path d="M3.5 2.7l2 1.8-2 1.8z" fill="#c1272d"/></svg><span>Your website on subscription autopilot with free unlimited support and updates.</span></li>
    <li><svg width="9" height="9" viewBox="0 0 9 9"><circle cx="4.5" cy="4.5" r="3.8" fill="none" stroke="#c1272d"/><path d="M3.5 2.7l2 1.8-2 1.8z" fill="#c1272d"/></svg><span>Delivered by professionals.</span></li>
  </ul>
</article>

<article class="card card-b">
  <div class="badge"><div class="badge-inner"><svg width="48" height="52" viewBox="0 0 48 52"><path d="M17 4l4 4 3-5 3 5 4-4-2 10H19z" fill="#c1272d"/><path d="M19 16h10c10 6 16 14 16 24 0 8-6 10-21 10S3 48 3 40c0-10 6-18 16-24z" fill="#c1272d"/><text x="24" y="41" text-anchor="middle" font-family="Arimo,sans-serif" font-size="18" font-weight="700" fill="#fff">$</text></svg></div></div>
  <h2 class="card-title">WHAT DOES IT COST?</h2>
  <ul class="points">
    <li><svg width="10" height="9" viewBox="0 0 10 9"><path d="M1 1h6v4H1zM7 2h2v2H7M1 7h7" fill="none" stroke="#c1272d" stroke-width="1.2"/></svg><span>a day and guaranteed less than a really good night out withthe gang</span></li>
    <li><svg width="10" height="14" viewBox="0 0 10 14"><path d="M1 1h8c0 4-2 6-4 6S1 5 1 1zM5 7v5M2 13h6" fill="none" stroke="#c1272d" stroke-width="1.2"/></svg><span>See price details here</span></li>
  </ul>
  <span class="btn order-btn">ORDER</span>
</article>

<article class="card card-c">
  <div class="badge"><div class="badge-inner"><svg width="54" height="54" viewBox="0 0 54 54"><circle cx="27" cy="27" r="24" fill="none" stroke="#c1272d" stroke-width="3.5"/><circle cx="19" cy="22" r="3" fill="#c1272d"/><circle cx="35" cy="22" r="3" fill="#c1272d"/><path d="M17 39c5-7 15-7 20 0" fill="none" stroke="#c1272d" stroke-width="3.5" stroke-linecap="round"/></svg></div></div>
  <h2 class="card-title">IF YOU ARE UNHAPPY?</h2>
  <ul class="points">
    <li><svg width="9" height="9" viewBox="0 0 9 9"><circle cx="4.5" cy="4.5" r="3.8" fill="none" stroke="#c1272d"/><path d="M3.5 2.7l2 1.8-2 1.8z" fill="#c1272d"/></svg><span>Cancel the same day, we will refund you all your money and buy you a year of Tunewave subscription</span></li>
  </ul>
  <div class="partner">Tunewave</div>
</article>

<article class="card card-d">
  <h2 class="calc-title">TEST YOUR WEBSITE NOW!</h2>
  <p class="calc-sub">How many more customers could you get every month?</p>
  <div class="field" style="top:76px"><label>Visitors per month :</label><span class="box"></span><span class="hint">(If you can't remember, put in 10 000. Number of visitors to your website monthly.)</span></div>
  <div class="field" style="top:117px"><label>Current conversion rate in %"</label><span class="box"></span><span class="hint">(If you can't remember put in a 1. The percentage of the visitors to your web that ends up doing service. It is usually 15%)</span></div>
  <div class="field" style="top:163px"><label>Improve conversion rate, 13%"</label><span class="box"></span><span class="hint">(let's aim for 13%, a typical increase is around 2%. Better web has a clear purpose, is up to date. Fill in what your goal is with conversion inc...</span></div>
  <div class="field" style="top:209px"><label>Average purchase in SEK</label><span class="box">SEK<svg width="6" height="5" viewBox="0 0 6 5" style="position:absolute;right:5px;top:6px"><path d="M0 0h6L3 5z" fill="#555"/></svg></span><span class="hint">what is theaverage amount a customer spends with your company within the first year, it can 000+, if you can't remember then guestimate</span></div>
  <span class="btn calc-btn">CALCULATE!</span>
</article>

<section class="cta-band"><div class="cta">SEE PRICES AND DETAILS FOR “MOST CONVENIENT WEB EVER”</div></section>

<footer class="footer">
  <nav class="foot-nav">Home &nbsp;| &nbsp;How it Work &nbsp;| &nbsp;About Us &nbsp;| &nbsp;FAQs &nbsp;| &nbsp;Privacy Policy &nbsp;| &nbsp;What Pepople Think ? &nbsp;| &nbsp;Order &nbsp;| &nbsp;Contact Us</nav>
  <p class="copy">Copy Rights 2014 Site Launch.All Rights Reserved.</p>
  <div class="social"><span style="background:#3b5b9a"></span><span style="background:#e0588c"></span><span style="background:#55acee"></span><span style="background:#4a7aa3"></span><span style="background:#d9574a"></span></div>
</footer>
</body>
</html>
```